VORTEQ

It’s is a startup business. We design and build new products.

Target Market(s)

For my first two products, they are targeting the laundry market, hanger accessory, and new modern style clothes dryer. I also have a Pet Treat product at patent stage, and there are other products not yet started but will be more engineering based. Therefore from young adults to older population

Industry/Entity Type

Colours of website to match the logo (att)

Coding

Coded - Design and coding required

Number of Pages Required

1 page

Font styles to use
Other font styles liked:
• Some of the same font as the logo

Colors

Designer to choose colors to be used in the design.

Requirements
Must have
• An upbeat vibe - the logo looks great so inline with that !
Should not have
• anything old fashioned and old style fonts

```html
<!DOCTYPE html>
<html lang="en">
<head>
<meta charset="utf-8">
<title>VORTEQ — Innovating Everyday Essentials</title>
<link rel="stylesheet" href="https://fonts.googleapis.com/css2?family=Michroma&family=Poppins:wght@400;500;600&display=swap">
<style>
:root{
  --bg:#04070a;
  --bar:#3c3c3f;
  --white:#ffffff;
  --cyan:#1ec8cf;
  --blue:#10b3e3;
  --frame:#1a9fd4;
  --ink:#0b3a55;
  --muted:#d8dde2;
}
*{margin:0;padding:0;box-sizing:border-box}
html,body{width:1200px;height:3809px;overflow:hidden;background:var(--bg)}
body{position:relative;font-family:"Poppins",sans-serif;color:var(--white)}
.display{font-family:"Michroma",sans-serif;letter-spacing:1px;text-transform:uppercase;font-weight:400;-webkit-text-stroke:0.7px currentColor}
.accent{color:var(--cyan)}

.glow{position:absolute;border-radius:50%;filter:blur(60px);pointer-events:none}

/* header */
.site-header{position:absolute;left:0;top:0;width:1200px;height:99px;background:var(--bar)}
.brand{position:absolute;display:flex;align-items:center;gap:10px;font-family:"Michroma",sans-serif;font-size:24px;letter-spacing:3px;color:var(--white)}
.brand-dot{width:16px;height:16px;border-radius:50%;background:var(--cyan)}
.site-header .brand{left:92px;top:34px}
.main-nav{position:absolute;left:388px;top:41px;display:flex;gap:22px;font-size:13.4px;font-weight:600;letter-spacing:.2px}
.btn-solid{position:absolute;display:flex;align-items:center;justify-content:center;background:linear-gradient(90deg,var(--blue),var(--cyan));color:#03202b;font-weight:600;font-size:12.5px;border-radius:5px}
.site-header .btn-solid{left:866px;top:28px;width:229px;height:44px}

/* hero */
.hero-title{position:absolute;left:0;width:1200px;top:153px;text-align:center;font-size:26.5px;line-height:41px;letter-spacing:1.5px}
.hero .btn-solid{left:485px;top:257px;width:230px;height:45px;font-size:12px}
.hero-visual{position:absolute;left:200px;top:325px;width:786px;height:421px;background:radial-gradient(ellipse at 45% 45%,#2a2d33 0%,#121418 45%,#05070a 80%)}
.hero-bar{position:absolute;left:269px;top:745px;width:717px;height:8px;background:var(--cyan)}
.hero-dots{position:absolute;left:1099px;top:369px;display:flex;flex-direction:column;gap:8px}
.hero-dots span{width:12px;height:12px;border-radius:50%;background:var(--cyan)}
.hero-dots span:first-child{background:var(--white)}

/* product rows */
.product{position:absolute;left:0;width:1200px;height:430px}
.product .frame{position:absolute;width:414px;height:412px;top:9px;border:2px solid var(--frame)}
.product .photo{position:absolute;top:0;width:412px;height:409px}
.product .title{position:absolute;top:24px;font-size:26px;line-height:36px;letter-spacing:2px}
.product .title .accent{display:block;margin-left:-8px;margin-top:5px}
.product .rule{position:absolute;top:84px;width:2px;height:300px;background:linear-gradient(#8a8f94,#3a3e42)}
.product .rule::after{content:"";position:absolute;left:0;bottom:0;width:24px;height:2px;background:#8a8f94}
.product p{position:absolute;top:134px;width:362px;font-size:13px;line-height:21.4px;text-align:justify;color:var(--muted)}
.btn-outline{position:absolute;top:356px;width:156px;height:46px;border:2px solid var(--white);display:flex;align-items:center;justify-content:center;font-size:12px;font-weight:600}

.img-left .frame{left:152px}
.img-left .photo{left:165px}
.img-left .title{left:729px}
.img-left .rule{left:693px}
.img-left p,.img-left .btn-outline{left:729px}

.img-right .frame{left:665px}
.img-right .photo{left:677px}
.img-right .title{left:200px}
.img-right .rule{left:165px}
.img-right p,.img-right .btn-outline{left:200px}

/* band */
.values{position:absolute;left:108px;top:2842px;width:984px;height:312px;background:linear-gradient(90deg,#06b4e2,#27cbc8)}
.values h2{position:absolute;left:0;width:984px;top:72px;text-align:center;font-size:26px;color:#062433;letter-spacing:1.5px}
.values .lead{position:absolute;left:130px;width:724px;top:130px;text-align:center;font-size:13.4px;line-height:21px;font-weight:500;color:#062433}
.values .pillars{position:absolute;left:0;top:217px;width:984px;height:95px;border-top:1.5px solid rgba(8,60,85,.55);display:flex}
.pillars div{height:95px;display:flex;align-items:center;justify-content:center;font-size:20px;font-weight:600;color:var(--ink);border-right:1.5px solid rgba(8,60,85,.55)}
.pillars div:last-child{border-right:none}

/* testimonials */
.testimonials h2{position:absolute;left:0;width:1200px;top:3243px;text-align:center;font-size:26px;letter-spacing:1.5px}
.testimonials blockquote{position:absolute;left:205px;width:790px;top:3326px;text-align:center;font-size:13px;line-height:21.4px;color:var(--muted)}
.testimonials cite{position:absolute;left:0;width:1200px;top:3410px;text-align:center;font-style:normal;font-size:14px;font-weight:600}
.t-dots{position:absolute;left:578px;top:3461px;display:flex;gap:3px}
.t-dots span{width:9px;height:9px;border-radius:50%;background:var(--cyan)}
.t-dots span:last-child{background:var(--white)}

/* footer */
.site-footer{position:absolute;left:0;top:3568px;width:1200px;height:241px;background:var(--bar)}
.site-footer .brand{left:0;width:1200px;justify-content:center;top:43px}
.foot-nav{position:absolute;left:0;width:1200px;top:113px;display:flex;justify-content:center;gap:23px;font-size:14px;font-weight:600}
.foot-line{position:absolute;left:0;top:150px;width:1200px;height:1px;background:rgba(255,255,255,.35)}
.foot-meta{position:absolute;top:168px;font-size:11.5px;font-weight:500}
</style>
</head>
<body>

<div class="glow" style="left:-180px;top:1100px;width:420px;height:700px;background:rgba(20,120,150,.28)"></div>
<div class="glow" style="left:1000px;top:650px;width:360px;height:500px;background:rgba(20,130,160,.25)"></div>
<div class="glow" style="left:-200px;top:1900px;width:420px;height:600px;background:rgba(20,120,150,.22)"></div>

<header class="site-header">
  <div class="brand"><span class="brand-dot"></span>VORTEQ</div>
  <nav class="main-nav"><span>HOME</span><span>PRODUCTS</span><span>INNOVATION</span><span>ABOUT US</span><span>CONTACT US</span></nav>
  <a class="btn-solid">DISCOVER OUR INNOVATIONS</a>
</header>

<section class="hero">
  <h1 class="hero-title display">Innovating Everyday Essentials<br>With Engineering Precision</h1>
  <a class="btn-solid">EXPLORE OUR PRODUCTS</a>
  <div class="hero-visual" role="img" aria-label="Sleek black and copper hair dryer on a dark background"></div>
  <div class="hero-bar"></div>
  <div class="hero-dots"><span></span><span></span><span></span><span></span></div>
</section>

<section class="product img-left" style="top:869px">
  <div class="frame"></div>
  <div class="photo" role="img" aria-label="Futuristic white wardrobe room with glowing hanger display" style="background:linear-gradient(135deg,#cfe4f6,#8fb8e4 55%,#d8ebfa)"></div>
  <h2 class="title display">Hanger<span class="accent">Accessory</span></h2>
  <div class="rule"></div>
  <p>Lorem ipsum dolor sit amet, consectetur adipiscing elit, sed do eiusmod tempor incididunt ut labore et dolore magna aliqua. Ut enim ad minim veniam, quis nostrud exercitation ullamco laboris nisi ut aliquip ex ea commodo consequat. Duis aute irure dolor in reprehenderit in voluptate velit esse cillum dolore eu fugiat nulla pariatur. Excepteur sint occaecat cupidatat non proident, sunt in culpa qui officia deserunt mollit anim id est laborum</p>
  <a class="btn-outline">VIEW MORE</a>
</section>

<section class="product img-right" style="top:1349px">
  <div class="frame"></div>
  <div class="photo" role="img" aria-label="Modern white clothes dryer with glowing blue drum" style="background:linear-gradient(135deg,#d6eef8,#7fc6e6 50%,#e6f4fa)"></div>
  <h2 class="title display">Modern<span class="accent">Clothes Dryer</span></h2>
  <div class="rule"></div>
  <p>Lorem ipsum dolor sit amet, consectetur adipiscing elit, sed do eiusmod tempor incididunt ut labore et dolore magna aliqua. Ut enim ad minim veniam, quis nostrud exercitation ullamco laboris nisi ut aliquip ex ea commodo consequat. Duis aute irure dolor in reprehenderit in voluptate velit esse cillum dolore eu fugiat nulla pariatur. Excepteur sint occaecat cupidatat non proident, sunt in culpa qui officia deserunt mollit anim id est laborum</p>
  <a class="btn-outline">VIEW MORE</a>
</section>

<section class="product img-left" style="top:1840px">
  <div class="frame"></div>
  <div class="photo" role="img" aria-label="Three clear dispensers filled with colourful pet treats" style="background:linear-gradient(90deg,#e2e0dc,#cbc6be 30%,#c4cfa8 50%,#d9b68a 75%,#e4e1dc)"></div>
  <h2 class="title display">Pet Treat<span class="accent">Product</span></h2>
  <div class="rule"></div>
  <p>Lorem ipsum dolor sit amet, consectetur adipiscing elit, sed do eiusmod tempor incididunt ut labore et dolore magna aliqua. Ut enim ad minim veniam, quis nostrud exercitation ullamco laboris nisi ut aliquip ex ea commodo consequat. Duis aute irure dolor in reprehenderit in voluptate velit esse cillum dolore eu fugiat nulla pariatur. Excepteur sint occaecat cupidatat non proident, sunt in culpa qui officia deserunt mollit anim id est laborum</p>
  <a class="btn-outline">VIEW MORE</a>
</section>

<section class="product img-right" style="top:2320px">
  <div class="frame"></div>
  <div class="photo" role="img" aria-label="Hand using a phone app to control a washing machine" style="background:linear-gradient(135deg,#8c8a86,#c9c6c0 45%,#5c5a58)"></div>
  <h2 class="title display">Laundry<span class="accent">Market.</span></h2>
  <div class="rule"></div>
  <p>Lorem ipsum dolor sit amet, consectetur adipiscing elit, sed do eiusmod tempor incididunt ut labore et dolore magna aliqua. Ut enim ad minim veniam, quis nostrud exercitation ullamco laboris nisi ut aliquip ex ea commodo consequat. Duis aute irure dolor in reprehenderit in voluptate velit esse cillum dolore eu fugiat nulla pariatur. Excepteur sint occaecat cupidatat non proident, sunt in culpa qui officia deserunt mollit anim id est laborum</p>
  <a class="btn-outline">VIEW MORE</a>
</section>

<section class="values">
  <h2 class="display">Engineering Meets Innovation</h2>
  <p class="lead">At Vorteq, we create cutting-edge products that blend functionality with aesthetics. From laundry solutions to pet care and beyond, our designs simplify and enhance everyday life.</p>
  <div class="pillars">
    <div style="width:251px">Smart Design</div>
    <div style="width:232px">Sustainability</div>
    <div style="width:257px">Focused Innovation</div>
    <div style="width:244px">Future Thinking</div>
  </div>
</section>

<section class="testimonials">
  <h2 class="display">What People <span class="accent">Are Saying</span></h2>
  <blockquote>Lorem ipsum dolor sit amet, consectetur adipiscing elit, sed do eiusmod tempor incididunt ut labore et dolore magna aliqua. Ut enim ad minim veniam, quis nostrud exercitation ullamco laboris nisi ut aliquip ex ea commodo consequat. Duis aute irure dolor in reprehenderit in voluptate velit esse cillum dolore e</blockquote>
  <cite>MARA QUILL</cite>
  <div class="t-dots"><span></span><span></span><span></span><span></span></div>
</section>

<footer class="site-footer">
  <div class="brand"><span class="brand-dot"></span>VORTEQ</div>
  <nav class="foot-nav"><span>HOME</span><span>PRODUCTS</span><span>INNOVATION</span><span>ABOUT US</span><span>CONTACT US</span></nav>
  <div class="foot-line"></div>
  <div class="foot-meta" style="left:180px">Copyright@2025.All Rights Reserved</div>
  <div class="foot-meta" style="left:543px">Sign up Our Newsletter</div>
  <div class="foot-meta" style="left:847px">Snapvelo | Linqora | Vidrunix</div>
</footer>

</body>
</html>
```